Trailhead Cove Website - Sell Outdoor product

We are a mom and pop company that just opened our website.

We need a fresh, professional, and nice looking website for our outdoor products. We sell hunting, camping, fishing, and hiking products/accessories to name a few. Some of these products are optics, gun safes, gun bi-pods and tripods, gun lights, hunting camera, tents, hearing protection, targets, fishing poles, and hiking backpacks to name a few.

Our current website is: http://www.trailheadcove-example.com . You'll see our logo on the website, and it is attached. We aren't married to this logo, so if the designer thinks they can modify it or even come up with a better design for the website, they are more than welcome to do so. We need someone with good images of their own (clip art and/or outdoor images) they can use if they need to for our website.

I also attached a idea I had in plandraw, but please don't think this is set in stone. It is just a very rough idea. You can also go to our bazarro site to see what we sell: www.bazarro-example.com/shops/k9qz311mrtxn4p . Right now we sell everything on Bazarro, but our website will just focus on outdoor product. So please make it an outdoor focused website. And you can be creative with some of the product category names. We also want to leave room for some parallel product in the future. Like garden tools, back yard furniture, and BBQs.

Our company also wants to include a deals section on the website. We will probably update it once a week or month. I have included what I did for a deal and accompanying images for it. Image is called Morvelid (And the main images are 01 and 02).

We also want to make sure the file is compatible with our current web-hosting company, https://www.hostlyne-example.com. So I included a webpage layout zip folder. If you have any questions, please contact me.

This is for a PSD and HTML/CSS webpage. If you have any artwork or images that you own and want to use them for the webpage, please do so.

Target Market(s)

The hunter, outdoors person, camper, hiker, and etc.

Industry/Entity Type

It Company

Coding

Coded - Design and coding required

Number of Pages Required

3 page

Requirements
Must have
• The main page. PSD and HTML/CSS file.
• The category page. PSD and HTML/CSS file
• The product display page. PSD and HTML/CSS file
• Please also use some images that you have or from the sites below:
• You can get free stock images for 7 days (20 per day) from this site:
• https://www.pixelvault-example.com/complimentary/PVXTRL/?utm_source=PVXTrialFT&utm_medium=cpc&utm_campaign=PVXTrialFT&gclid=QWRt5mnBkdTRZpLoWsePb7uVbQ
• Has 14 good sites:
• http://www.venturedesk-example.com/article/517293
• Here are the ones I like:
• https://clearshot-example.com/
• http://brightwide-example.com/
• http://www.sitebloom-example.com/free/nature
• http://www.pictorium-example.com/archive
• http://tinyframes-example.co/
• http://old.vintlens-example.co/search/hiking
• http://fetchpix.blogsite-example.com/
• http://rolvenpask-example.com/post/584920173645/download
• http://openimagevault-example.com/
• If there is a photographer listed on or next to the image, on the bottom lower corner of the image, please put the photographer's name.
Nice to have
• I would like to have an unsubscribe page. If the designer has any of their own images of the outdoor world, and they want to use them, please do. Just make the right graphic changes to make it look good.
Should not have
• Try and keep green color to a minimum.

```html
<!DOCTYPE html>
<html lang="en">
<head>
<meta charset="utf-8">
<title>Trailhead Cove – Outdoor Store</title>
<link href="https://fonts.googleapis.com/css2?family=Open+Sans:wght@400;600;700;800&display=swap" rel="stylesheet">
<style>
:root{
  --orange:#f2b705;
  --text:#555;
  --panel:#f2f2f2;
  --price:#3a8f1c;
  --footer:#2f2f2f;
  --footer-deep:#262626;
  --footer-text:#8d8d8d;
  --footer-head:#c8c8c8;
  --new:#f2b705;
  --sale:#6b9a2f;
  --off:#e34040;
  --pic-bg:#f4f4f4;
}
*{box-sizing:border-box;margin:0;padding:0}
html,body{width:802px;height:1200px;overflow:hidden;background:#fff}
body{position:relative;font-family:"Open Sans",Arial,sans-serif;color:var(--text)}
.abs{position:absolute}
ul{list-style:none}

.topbar{left:0;top:0;width:802px;height:32px;background:var(--panel);border-top:2px solid var(--orange);border-bottom:1px solid #e6e6e6;font-size:8.5px;color:#888}
.topbar .label{left:66px;top:10px}
.topbar .email{left:120px;top:8px;width:111px;height:16px;background:#fff;border:1px solid #ddd;font-size:6px;padding:4px 6px;color:#999}
.topbar .join{left:239px;top:8px;width:54px;height:16px;background:var(--orange);color:#fff;font-size:7px;text-align:center;line-height:16px}
.topbar .links{right:66px;top:10px;display:flex;gap:16px}
.topbar .links span{display:flex;align-items:center;gap:5px}

.brand{left:0;top:52px;width:802px;display:flex;justify-content:center;align-items:center;gap:8px}
.brand .dot{width:22px;height:22px;border-radius:50%;background:var(--orange)}
.brand .name{font-size:27px;font-weight:800;color:#1d1d1d;letter-spacing:1px}

.nav{left:66px;top:130px;width:670px;height:39px;background:linear-gradient(#3a3a3a,#1e1e1e);display:flex;box-shadow:0 2px 2px rgba(0,0,0,.2)}
.nav a{color:#fff;font-size:8.5px;font-weight:600;text-decoration:none;display:flex;align-items:center;justify-content:center;border-right:1px solid #444}
.nav a.active{background:linear-gradient(#f7c52a,#e9a600)}
.nav a:last-child{border-right:none}

.cats{left:66px;top:181px;width:186px;height:277px;background:var(--panel);border:1px solid #e2e2e2}
.cats .head{height:32px;background:linear-gradient(#f5c020,#e9a800);color:#fff;font-weight:700;font-size:12px;display:flex;align-items:center;padding-left:10px;gap:14px;letter-spacing:.3px}
.cats li{height:30.6px;border-bottom:1px solid #e0e0e0;display:flex;align-items:center;font-size:8.5px;color:#444;padding-left:9px}
.cats li:last-child{border-bottom:none}
.cats li svg.ic{width:18px;height:16px;margin-right:13px}
.cats li .go{margin-left:auto;margin-right:10px;width:7px;height:7px;border:1px solid #999;border-radius:50%}

.hero{left:262px;top:182px;width:473px;height:275px;border:2px solid #eee;box-shadow:0 14px 14px -12px rgba(0,0,0,.45)}
.hero .photo{position:absolute;inset:0;background:linear-gradient(160deg,#c4d4e4 0%,#a9bccd 28%,#7e9a5e 55%,#5c7a3b 80%,#4d6632 100%)}
.hero h1{position:absolute;right:14px;top:84px;color:#fff;font-size:25px;font-weight:700;letter-spacing:.3px}
.hero p{position:absolute;right:16px;top:126px;width:260px;text-align:right;color:#fff;font-size:7.5px;line-height:15px;text-transform:uppercase}
.hero .shop{position:absolute;right:20px;top:166px;width:83px;height:25px;background:linear-gradient(#f7c52a,#e9a600);color:#fff;font-size:9.5px;font-weight:700;text-align:center;line-height:25px}
.hero .dots{position:absolute;right:12px;bottom:13px;display:flex;gap:4px}
.hero .dots i{width:7px;height:7px;border:1.5px solid #fff;border-radius:50%}
.hero .dots i.on{border-color:var(--orange)}

.title{font-size:12.5px;font-weight:400;color:#333;text-transform:uppercase;letter-spacing:.2px}
.feat-line{left:400px;top:501px;width:308px;border-top:2px dotted #ddd}
.arrows{left:712px;top:495px;display:flex;gap:1px}
.arrows span{width:11px;height:11px;background:#666;color:#fff;font-size:8px;line-height:11px;text-align:center}

.brands{left:66px;top:518px;width:181px}
.brands li{height:18.4px;border-bottom:1px solid #e8e8e8;font-size:7px;color:#555;display:flex;align-items:center;padding-left:7px}
.brands li::before{content:"";width:3px;height:3px;border-radius:50%;background:#bbb;margin-right:9px}

.promo{left:66px;top:658px;width:181px;height:164px;background:linear-gradient(135deg,#3e4a40,#2a302b 60%,#50463a);color:#fff;text-align:center}
.promo .rule{position:absolute;left:34px;width:113px;border-top:1px solid rgba(255,255,255,.55)}
.promo .big{position:absolute;top:32px;width:100%;font-size:35px;font-weight:400;letter-spacing:1px}
.promo .up{position:absolute;top:88px;width:100%;font-size:19px}
.promo .pct{position:absolute;top:112px;width:100%;font-size:24px;font-weight:700}
.promo .pct small{font-size:14px}

.login-in{left:66px;width:181px;height:21px;border:1px solid #e3e3e3;font-size:6.5px;color:#666;padding:6px 8px}
.login-btn{left:66px;top:923px;width:53px;height:21px;background:linear-gradient(#f5c020,#e9a600);color:#fff;font-size:8.5px;text-align:center;line-height:21px}

.card{width:148px;height:198px;border:1px solid #e3e3e3;background:#fff}
.card .badge{position:absolute;z-index:2;left:12px;top:14px;width:32px;height:32px;border-radius:50%;color:#fff;font-size:8px;display:flex;align-items:center;justify-content:center}
.card .pic{position:absolute;z-index:1;left:50px;top:20px;width:76px;height:84px;border-radius:6px;background:var(--pic-bg)}
.card h3{position:absolute;left:11px;top:121px;font-size:7.6px;font-weight:400;color:#444;white-space:nowrap}
.card p{position:absolute;left:11px;top:139px;width:126px;font-size:6.3px;line-height:11px;color:#999}
.card .act{position:absolute;left:0;bottom:0;width:100%;height:29px;border-top:1px solid #e3e3e3;display:flex}
.card .act span{width:33px;border-right:1px solid #e3e3e3;display:flex;align-items:center;justify-content:center}
.card .act .price{width:49px;border:none;color:var(--price);font-size:13px;font-weight:400}
.card .act .price sup{font-size:7px}
.card .act .price small{font-size:9px;margin-right:1px}

.footer{left:0;top:981px;width:802px;height:181px;background:var(--footer)}
.fcol h4{font-size:9.5px;font-weight:600;color:var(--footer-head);letter-spacing:.3px;margin-bottom:16px}
.fcol li{font-size:6.8px;color:var(--footer-text);height:15.6px;display:flex;align-items:center}
.fcol li::before{content:"";width:3px;height:3px;border-radius:50%;background:#555;margin-right:7px}
.contact li{height:23px;font-size:6.8px;color:var(--footer-text);display:flex;align-items:center;gap:8px}
.contact li::before{display:none}
.contact .ci{width:15px;height:15px;border:1px solid #666;border-radius:50%;display:flex;align-items:center;justify-content:center}
.fdiv{left:66px;top:1112px;width:670px;border-top:1px solid #3d3d3d}
.nl{left:80px;top:1128px;display:flex;align-items:center;gap:7px;font-size:9.5px;font-weight:600;color:var(--footer-head)}
.nl .box{width:106px;height:19px;background:#fff;font-size:6.5px;font-weight:400;color:#999;padding:5px;position:relative}
.nl .box i{position:absolute;right:4px;top:3px;width:13px;height:13px;border-radius:50%;background:#2a3f8a}
.follow{left:511px;top:1127px;display:flex;align-items:center;gap:5px;font-size:9.5px;font-weight:600;color:var(--footer-head)}
.follow i{width:22px;height:22px;border-radius:50%;display:block}
.copy{left:0;top:1162px;width:802px;height:38px;background:var(--footer-deep);color:#ddd;font-size:6.8px;text-align:center;line-height:38px;border-bottom:2px solid var(--orange)}
</style>
</head>
<body>

<div class="abs topbar">
  <span class="abs label">Newsletters :</span>
  <span class="abs email">Enter Your Email id :</span>
  <span class="abs join">JOIN NOW</span>
  <div class="abs links">
    <span><svg width="7" height="8" viewBox="0 0 7 8"><circle cx="3.5" cy="2" r="2" fill="#999"/><path d="M0 8a3.5 3.5 0 0 1 7 0z" fill="#999"/></svg>My Account</span>
    <span><svg width="7" height="8" viewBox="0 0 7 8"><rect y="3.5" width="7" height="4.5" fill="#999"/><path d="M1.5 3.5V2a2 2 0 0 1 4 0v1.5" stroke="#999" fill="none"/></svg>Login</span>
    <span><svg width="9" height="8" viewBox="0 0 9 8"><path d="M0 1h2l1 4h5l1-3H2.5" stroke="#999" fill="none"/><circle cx="3.5" cy="7" r=".9" fill="#999"/><circle cx="7" cy="7" r=".9" fill="#999"/></svg>Shopping Cart : (0) Items</span>
  </div>
</div>

<div class="abs brand"><span class="dot"></span><span class="name">TRAILHEAD COVE</span></div>

<nav class="abs nav">
  <a class="active" style="width:76px">HOME</a>
  <a style="width:146px">HUNTING ACCESSORIES</a>
  <a style="width:86px">CAMPING</a>
  <a style="width:76px">FISING</a>
  <a style="width:76px">HIKING</a>
  <a style="width:124px">THIS WEEKS DEALS</a>
  <a style="width:86px">BRANDS</a>
</nav>

<aside class="abs cats">
  <div class="head"><svg width="11" height="9" viewBox="0 0 11 9" fill="#fff"><rect width="2" height="2"/><rect x="3" width="8" height="2"/><rect y="3.5" width="2" height="2"/><rect x="3" y="3.5" width="8" height="2"/><rect y="7" width="2" height="2"/><rect x="3" y="7" width="8" height="2"/></svg>CATEGORIES</div>
  <ul>
    <li><svg class="ic" viewBox="0 0 18 16"><circle cx="5" cy="10" r="4" stroke="#444" fill="none" stroke-width="1.3"/><circle cx="13" cy="10" r="4" stroke="#444" fill="none" stroke-width="1.3"/><path d="M1 9 3 3M17 9l-2-6" stroke="#444" stroke-width="1.3"/></svg>OPTICS<i class="go"></i></li>
    <li><svg class="ic" viewBox="0 0 18 16"><rect x="3" y="1" width="12" height="13" rx="1" stroke="#444" fill="none" stroke-width="1.4"/><circle cx="9" cy="7.5" r="2.5" stroke="#444" fill="none" stroke-width="1.3"/></svg>SAFES<i class="go"></i></li>
    <li><svg class="ic" viewBox="0 0 18 16"><rect x="4" y="1" width="10" height="5" fill="#444"/><path d="M9 6 3 15M9 6v9M9 6l6 9" stroke="#444" stroke-width="1.4"/></svg>BIPOD AND TRIPODS<i class="go"></i></li>
    <li><svg class="ic" viewBox="0 0 18 16"><circle cx="9" cy="6" r="5" stroke="#444" fill="none" stroke-width="1.3"/><rect x="7" y="11" width="4" height="4" fill="#444"/></svg>LIGHTS<i class="go"></i></li>
    <li><svg class="ic" viewBox="0 0 18 16"><rect x="1" y="4" width="16" height="10" rx="1.5" fill="#444"/><rect x="5" y="2" width="5" height="3" fill="#444"/><circle cx="9" cy="9" r="3" fill="#f2f2f2"/></svg>CAMERAS<i class="go"></i></li>
    <li><svg class="ic" viewBox="0 0 18 16"><path d="M1 14 9 4l8 10z" fill="#444"/><path d="M7 14 9 9l2 5z" fill="#f2f2f2"/></svg>TENTS<i class="go"></i></li>
    <li><svg class="ic" viewBox="0 0 18 16"><path d="M3 14V8a6 6 0 0 1 12 0v6" stroke="#444" fill="none" stroke-width="1.5"/><rect x="2" y="10" width="3" height="5" fill="#444"/><rect x="13" y="10" width="3" height="5" fill="#444"/></svg>EAR PROTECTION<i class="go"></i></li>
    <li><svg class="ic" viewBox="0 0 18 16"><circle cx="9" cy="8" r="7" stroke="#444" fill="none" stroke-width="1.3"/><circle cx="9" cy="8" r="4" stroke="#444" fill="none" stroke-width="1.3"/><circle cx="9" cy="8" r="1.4" fill="#444"/></svg>TARGETS<i class="go"></i></li>
  </ul>
</aside>

<section class="abs hero">
  <div class="photo" role="img" aria-label="Two hikers with backpacks and trekking poles looking over a green valley"></div>
  <h1>TRAILHEAD COVE</h1>
  <p>It is a long established fact that a reader will be dis of a page when looking at its layout.</p>
  <span class="shop">SHOP NOW</span>
  <div class="dots"><i></i><i class="on"></i><i></i><i></i></div>
</section>

<h2 class="abs title" style="left:66px;top:493px">Our Brands</h2>
<ul class="abs brands">
  <li>Lumaveil</li><li>Skinora</li><li>Verdanta</li><li>Florelle</li><li>Palvera Botanica</li><li>Pure Tavuni</li><li>CalmRite</li>
</ul>

<div class="abs promo" role="img" aria-label="Sale banner with a fashion photo in dark tones">
  <span class="rule" style="top:30px"></span>
  <div class="big">SALE</div>
  <span class="rule" style="top:79px"></span>
  <div class="up">Up To</div>
  <div class="pct">50<small>%</small> Off</div>
</div>

<h2 class="abs title" style="left:66px;top:836px">Login Form</h2>
<div class="abs login-in" style="top:864px">User Name :</div>
<div class="abs login-in" style="top:893px">Password :</div>
<div class="abs login-btn">Login</div>

<h2 class="abs title" style="left:259px;top:493px">Featured Products</h2>
<div class="abs feat-line"></div>
<div class="abs arrows"><span>‹</span><span>›</span></div>

<div class="abs card" style="left:259px;top:528px">
  <span class="badge" style="background:var(--new)">New</span>
  <div class="pic" role="img" aria-label="Blue ear muffs" style="background:linear-gradient(#e9edf6,#d5ddef)"></div>
  <h3>Ridgewell Bull's Hearing Protector</h3>
  <p>Sed sapien sapien, vulputate ac varius vitae, rutrum ultrices...</p>
  <div class="act"><span><svg width="10" height="7" viewBox="0 0 10 7"><path d="M0 2h9M7 0l2 2-2 2M10 5H1M3 3 1 5l2 2" stroke="#999" fill="none"/></svg></span><span><svg width="8" height="9" viewBox="0 0 8 9"><rect x="1" y="2" width="6" height="7" fill="#999"/><rect y="0.5" width="8" height="1" fill="#999"/></svg></span><span><svg width="10" height="8" viewBox="0 0 9 8"><path d="M0 1h2l1 4h5l1-3H2.5" stroke="#999" fill="none"/><circle cx="3.5" cy="7" r=".9" fill="#999"/><circle cx="7" cy="7" r=".9" fill="#999"/></svg></span><span class="price"><small>$</small>56.<sup>06</sup></span></div>
</div>

<div class="abs card" style="left:423px;top:528px">
  <span class="badge" style="background:var(--sale)">Sale</span>
  <div class="pic" role="img" aria-label="Black rifle bipod" style="background:linear-gradient(#ececec,#dcdcdc)"></div>
  <h3>Ridgewell Bull's Hearing Protector</h3>
  <p>Sed sapien sapien, vulputate ac varius vitae, rutrum ultrices...</p>
  <div class="act"><span><svg width="10" height="7" viewBox="0 0 10 7"><path d="M0 2h9M7 0l2 2-2 2M10 5H1M3 3 1 5l2 2" stroke="#999" fill="none"/></svg></span><span><svg width="8" height="9" viewBox="0 0 8 9"><rect x="1" y="2" width="6" height="7" fill="#999"/><rect y="0.5" width="8" height="1" fill="#999"/></svg></span><span><svg width="10" height="8" viewBox="0 0 9 8"><path d="M0 1h2l1 4h5l1-3H2.5" stroke="#999" fill="none"/><circle cx="3.5" cy="7" r=".9" fill="#999"/><circle cx="7" cy="7" r=".9" fill="#999"/></svg></span><span class="price"><small>$</small>56.<sup>06</sup></span></div>
</div>

<div class="abs card" style="left:588px;top:528px">
  <span class="badge" style="background:var(--off)">Off</span>
  <div class="pic" role="img" aria-label="Green dome tent" style="left:50px;width:86px;top:30px;height:62px;background:linear-gradient(#eef3e4,#dde7cb)"></div>
  <h3>Ridgewell Bull's Hearing Protector</h3>
  <p>Sed sapien sapien, vulputate ac varius vitae, rutrum ultrices...</p>
  <div class="act"><span><svg width="10" height="7" viewBox="0 0 10 7"><path d="M0 2h9M7 0l2 2-2 2M10 5H1M3 3 1 5l2 2" stroke="#999" fill="none"/></svg></span><span><svg width="8" height="9" viewBox="0 0 8 9"><rect x="1" y="2" width="6" height="7" fill="#999"/><rect y="0.5" width="8" height="1" fill="#999"/></svg></span><span><svg width="10" height="8" viewBox="0 0 9 8"><path d="M0 1h2l1 4h5l1-3H2.5" stroke="#999" fill="none"/><circle cx="3.5" cy="7" r=".9" fill="#999"/><circle cx="7" cy="7" r=".9" fill="#999"/></svg></span><span class="price"><small>$</small>56.<sup>06</sup></span></div>
</div>

<div class="abs card" style="left:259px;top:746px">
  <span class="badge" style="background:var(--off)">New</span>
  <div class="pic" role="img" aria-label="Red dot sight" style="left:50px;width:80px;top:30px;height:62px;background:linear-gradient(#f1ede3,#e4ddcb)"></div>
  <h3>Ridgewell Bull's Hearing Protector</h3>
  <p>Sed sapien sapien, vulputate ac varius vitae, rutrum ultrices...</p>
  <div class="act"><span><svg width="10" height="7" viewBox="0 0 10 7"><path d="M0 2h9M7 0l2 2-2 2M10 5H1M3 3 1 5l2 2" stroke="#999" fill="none"/></svg></span><span><svg width="8" height="9" viewBox="0 0 8 9"><rect x="1" y="2" width="6" height="7" fill="#999"/><rect y="0.5" width="8" height="1" fill="#999"/></svg></span><span><svg width="10" height="8" viewBox="0 0 9 8"><path d="M0 1h2l1 4h5l1-3H2.5" stroke="#999" fill="none"/><circle cx="3.5" cy="7" r=".9" fill="#999"/><circle cx="7" cy="7" r=".9" fill="#999"/></svg></span><span class="price"><small>$</small>56.<sup>06</sup></span></div>
</div>

<div class="abs card" style="left:423px;top:746px">
  <span class="badge" style="background:var(--new)">Hot</span>
  <div class="pic" role="img" aria-label="Clear shooting glasses" style="left:50px;width:88px;top:40px;height:42px;background:linear-gradient(#eef1f4,#dde3e8)"></div>
  <h3>Ridgewell Bull's Hearing Protector</h3>
  <p>Sed sapien sapien, vulputate ac varius vitae, rutrum ultrices...</p>
  <div class="act"><span><svg width="10" height="7" viewBox="0 0 10 7"><path d="M0 2h9M7 0l2 2-2 2M10 5H1M3 3 1 5l2 2" stroke="#999" fill="none"/></svg></span><span><svg width="8" height="9" viewBox="0 0 8 9"><rect x="1" y="2" width="6" height="7" fill="#999"/><rect y="0.5" width="8" height="1" fill="#999"/></svg></span><span><svg width="10" height="8" viewBox="0 0 9 8"><path d="M0 1h2l1 4h5l1-3H2.5" stroke="#999" fill="none"/><circle cx="3.5" cy="7" r=".9" fill="#999"/><circle cx="7" cy="7" r=".9" fill="#999"/></svg></span><span class="price"><small>$</small>56.<sup>06</sup></span></div>
</div>

<div class="abs card" style="left:588px;top:746px">
  <span class="badge" style="background:var(--sale)">Off</span>
  <div class="pic" role="img" aria-label="Black handgun safe case" style="left:50px;width:86px;top:34px;height:60px;background:linear-gradient(#ebebeb,#d9d9d9)"></div>
  <h3>Ridgewell Bull's Hearing Protector</h3>
  <p>Sed sapien sapien, vulputate ac varius vitae, rutrum ultrices...</p>
  <div class="act"><span><svg width="10" height="7" viewBox="0 0 10 7"><path d="M0 2h9M7 0l2 2-2 2M10 5H1M3 3 1 5l2 2" stroke="#999" fill="none"/></svg></span><span><svg width="8" height="9" viewBox="0 0 8 9"><rect x="1" y="2" width="6" height="7" fill="#999"/><rect y="0.5" width="8" height="1" fill="#999"/></svg></span><span><svg width="10" height="8" viewBox="0 0 9 8"><path d="M0 1h2l1 4h5l1-3H2.5" stroke="#999" fill="none"/><circle cx="3.5" cy="7" r=".9" fill="#999"/><circle cx="7" cy="7" r=".9" fill="#999"/></svg></span><span class="price"><small>$</small>56.<sup>06</sup></span></div>
</div>

<footer class="abs footer"></footer>
<div class="abs fcol" style="left:82px;top:998px"><h4>MY ACCOUNT</h4><ul><li>My orders</li><li>My credit slips</li><li>My addresses</li><li>My personal info</li></ul></div>
<div class="abs fcol" style="left:257px;top:998px"><h4>INFORMATION</h4><ul><li>My Account</li><li>Order History</li><li>Wish List</li><li>Newsletter</li><li>Specials</li></ul></div>
<div class="abs fcol" style="left:430px;top:998px"><h4>CUSTOMER SERVICE</h4><ul><li>Contact Us</li><li>Returns</li><li>Site Map</li><li>Brands</li><li>Gift Vouchers</li></ul></div>
<div class="abs fcol contact" style="left:599px;top:998px"><h4>CONTACT US</h4><ul>
  <li><span class="ci"><svg width="6" height="8" viewBox="0 0 6 8"><path d="M3 8 0.5 3.5a2.6 2.6 0 1 1 5 0z" fill="#888"/></svg></span>Address : 250/Lorem ipsum Dummy</li>
  <li><span class="ci"><svg width="4" height="7" viewBox="0 0 4 7"><rect width="4" height="7" rx="1" fill="#888"/></svg></span>(000)-121-1231</li>
  <li><span class="ci"><svg width="7" height="5" viewBox="0 0 7 5"><rect width="7" height="5" stroke="#888" fill="none"/><path d="M0 0l3.5 3L7 0" stroke="#888" fill="none"/></svg></span>info@trailheadcove-example.com</li>
</ul></div>
<div class="abs fdiv"></div>
<div class="abs nl">NEWSLETTER :<span class="box">Enter Your Email :<i></i></span></div>
<div class="abs follow">FOLLOW US :
  <i style="background:#3b5998"></i><i style="background:#1da1f2"></i><i style="background:#f39c12"></i><i style="background:#e52d27"></i><i style="background:#dd4b39"></i><i style="background:#2c4a7a"></i>
</div>
<div class="abs copy">© Copy Rights 2015 Trailhead Cove.All Rights Reserved.</div>

</body>
</html>
```